Website for "Bright Morrow Ltd" cleaning bsuiness

We require a website to expose our business to the local market. We want to provide background on who we are and what we do but in an easily digestible way. We clean domestic and commercial premises and want to provide a list of all of our services to potential customers. We operate out of Warrington in the UK.

We would like the website to be animated in some way so that the experience of using it is not dull or mundane. This website needs to be an extension of our company.

Target Market(s)

30 - 60 year olds for Domestic plus commercial clients

Industry/Entity Type

Cleaning Service

Coding

Coded - Design and coding required

Number of Pages Required

4 page

Font styles to use
Sans Serif

Colors
0455a3
3176b5
85acd3
cfdeed
ffffff
000000
1b1b1b
c8c8c8
757575

Requirements
Must have
• Logo which has been provided. Theme based around the logo and its colours. Simple layout to avoid confusion.
Nice to have
• Animations where possible to impress the customer.
Should not have
• any pictures of cleaning equipment, fairies, maids etc

```html
<!DOCTYPE html>
<html lang="en">
<head>
<meta charset="utf-8">
<title>Bright Morrow Ltd – Cleaning Services</title>
<link rel="stylesheet" href="https://fonts.googleapis.com/css2?family=Open+Sans:wght@400;600&family=Raleway:wght@300;400&family=Roboto:wght@400;500&family=Roboto+Slab:wght@700&display=swap">
<style>
:root{
  --navy:#0a389c;
  --brand:#0455a3;
  --sky:#2a7fe2;
  --light:#85acd3;
  --pale:#cfdeed;
  --white:#ffffff;
  --ink:#1b1b1b;
  --grey:#757575;
  --line:#c8c8c8;
}
*{box-sizing:border-box;margin:0;padding:0}
html,body{width:1200px;height:3309px;overflow:hidden;background:var(--white)}
body{position:relative;font-family:"Open Sans",sans-serif;color:var(--ink)}
.abs{position:absolute}

/* hero */
.hero{position:absolute;left:0;top:0;width:1200px;height:781px;background:linear-gradient(120deg,#c9c9c9 0%,#9d9d9d 45%,#7d7d7d 70%,#b2b2b2 100%)}
.nav a{position:absolute;top:80px;font:400 17px "Roboto",sans-serif;color:var(--white);text-decoration:none;letter-spacing:.3px}
.nav a.active{color:var(--brand)}
.brand{position:absolute;left:430px;top:48px;width:340px;display:flex;align-items:center;justify-content:center;gap:12px}
.brand-dot{width:26px;height:26px;border-radius:50%;background:var(--brand)}
.brand-name{font:500 34px "Roboto",sans-serif;color:var(--brand)}
.hero-title{position:absolute;left:79px;top:272px;font:700 46px/53px "Roboto Slab",sans-serif;color:var(--navy)}
.hero-title span{color:var(--sky)}
.hero-rule{position:absolute;left:79px;width:391px;height:1px;background:#3a3a3a}
.hero-copy{position:absolute;left:79px;top:484px;width:391px;text-align:center;font-size:16px;line-height:28px;color:#222}
.arrow{position:absolute;top:364px;width:52px;height:52px;border-radius:50%;background:rgba(20,50,120,.75);display:flex;align-items:center;justify-content:center}
.dots{position:absolute;display:flex;gap:8px}
.dots i{display:block;border-radius:50%;border:2px solid #333}
.dots i.on{background:var(--brand);border-color:var(--brand)}

/* section headings */
.heading{position:absolute;left:0;width:1200px;text-align:center;font:400 37px "Raleway",sans-serif;letter-spacing:1px;color:var(--navy)}
.heading span{color:var(--sky)}
.intro{position:absolute;left:280px;width:640px;text-align:center;font-size:15px;line-height:27px;color:var(--grey)}
.btn{position:absolute;background:var(--navy);color:var(--white);font:400 17px "Roboto",sans-serif;display:flex;align-items:center;justify-content:center;border-radius:3px}

/* domestic */
.domestic{position:absolute;left:0;top:1110px;width:1200px;height:467px;background:linear-gradient(180deg,#3d63b8 0%,#2b55ad 100%)}
.domestic .heading{color:var(--white);top:42px}
.card{position:absolute;width:238px}
.photo{width:238px;height:167px}
.dom-title{margin-top:22px;font:400 20px "Roboto",sans-serif;color:var(--white)}
.dom-text{margin-top:8px;font-size:14.5px;line-height:24px;color:#d7e2f5}
.know{margin-top:14px;display:flex;align-items:center;gap:12px;font-size:13px;color:var(--white)}

/* commercial */
.com-title{margin-top:22px;text-align:center;font:400 20px "Roboto",sans-serif;color:var(--navy)}
.com-text{margin-top:8px;font-size:14.5px;line-height:24px;color:#333}
.more{margin-top:8px;text-align:center;font-size:20px;color:#222}
.com-rule{margin-top:16px;height:4px;background:var(--navy)}

/* testimonial */
.testimonial{position:absolute;left:0;top:2080px;width:1200px;height:263px;background:var(--sky)}
.t-head{position:absolute;left:100px;top:78px;width:260px;text-align:center;font:300 39px/48px "Raleway",sans-serif;letter-spacing:4px;color:var(--white)}
.t-divider{position:absolute;left:377px;top:38px;width:1px;height:165px;background:rgba(255,255,255,.35)}
.t-text{position:absolute;left:569px;top:75px;width:520px;font-size:14px;line-height:30px;color:var(--white)}

/* contact form */
.field{position:absolute;border:1.5px solid #4a6cc0;font-size:14px;color:#555;padding:6px 8px}

/* footer */
.footer{position:absolute;left:0;top:2903px;width:1200px;height:351px;background:var(--navy);color:var(--white)}
.f-head{position:absolute;top:50px;font:400 18px "Roboto",sans-serif}
.f-links a{position:absolute;left:79px;font-size:14px;color:var(--white);text-decoration:none}
.f-post{position:absolute;left:287px;display:flex;gap:10px}
.f-thumb{width:66px;height:62px;background:linear-gradient(135deg,#8a9bb8,#4b5f86)}
.f-post p{font-size:15px;line-height:19px;width:200px}
.f-news{position:absolute;left:598px;width:240px;font-size:15px;line-height:20px}
.f-read{position:absolute;left:598px;font-size:14px;padding-bottom:6px;border-bottom:1px solid rgba(255,255,255,.6);width:180px}
.f-contact{position:absolute;left:900px;width:240px;font-size:15px;line-height:22px}
.social{position:absolute;top:3165px;width:50px;height:50px;border-radius:50%}
.bottom{position:absolute;left:0;top:3254px;width:1200px;height:55px;background:var(--sky);color:var(--white);font-size:14px;display:flex;align-items:center;justify-content:center;letter-spacing:.5px}
</style>
</head>
<body>

<header class="hero" role="img" aria-label="Photo of a sofa being cleaned, soft grey upholstery">
  <nav class="nav">
    <a class="active" style="left:88px">HOME</a>
    <a style="left:190px">ABOUT</a>
    <a style="left:300px">SERVICES</a>
    <a style="left:810px">BLOG</a>
    <a style="left:893px">CONTACT</a>
  </nav>
  <div class="brand"><span class="brand-dot"></span><span class="brand-name">Bright Morrow Ltd</span></div>
  <h1 class="hero-title">Bright Morrow<br>Domestic and Commercial<br><span>Cleaning Services</span></h1>
  <div class="hero-rule" style="top:465px"></div>
  <p class="hero-copy">Lorem Ipsum is simply dummy text of the<br>printing and typesetting industry.</p>
  <div class="hero-rule" style="top:558px"></div>
  <div class="arrow" style="left:10px"><svg width="22" height="18" viewBox="0 0 22 18"><path d="M10 2 3 9l7 7M19 2l-7 7 7 7" fill="none" stroke="#fff" stroke-width="2.5"/></svg></div>
  <div class="arrow" style="left:1137px"><svg width="22" height="18" viewBox="0 0 22 18"><path d="M3 2l7 7-7 7M12 2l7 7-7 7" fill="none" stroke="#fff" stroke-width="2.5"/></svg></div>
  <div class="dots" style="left:557px;top:716px"><i style="width:24px;height:24px"></i><i class="on" style="width:24px;height:24px"></i><i style="width:24px;height:24px"></i></div>
</header>

<section class="welcome">
  <h2 class="heading" style="top:828px">WELCOME TO <span>BRIGHT MORROW CLEANING SERVICES</span></h2>
  <p class="intro" style="top:893px">Lorem Ipsum is simply dummy text of the printing and typesetting industry. Lorem Ipsum has been the industry's standard dummy text ever since the 1500s, when an unknown printer took a galley of type and scrambled it to make a type specimen book.</p>
  <div class="btn" style="left:496px;top:1006px;width:217px;height:62px">READ MORE</div>
</section>

<section class="domestic" role="img" aria-label="Blue tinted photo of a bright living room">
  <h2 class="heading">DOMESTIC SERVICES</h2>
  <div class="card" style="left:77px;top:117px">
    <div class="photo" role="img" aria-label="Photo of carpet cleaning" style="background:linear-gradient(135deg,#d9c7a8,#a68c68)"></div>
    <div class="dom-title">Carpet Cleaning</div>
    <p class="dom-text">Lorem Ipsum is simply dummy text of the printing typesetting</p>
    <div class="know">KNOW MORE <svg width="26" height="26" viewBox="0 0 26 26"><circle cx="13" cy="13" r="11.5" fill="none" stroke="#fff" stroke-width="1.5"/><path d="M11 8l5 5-5 5" fill="none" stroke="#fff" stroke-width="1.8"/></svg></div>
  </div>
  <div class="card" style="left:346px;top:117px">
    <div class="photo" role="img" aria-label="Photo of ironing at home" style="background:linear-gradient(135deg,#f3ede6,#d89a94)"></div>
    <div class="dom-title">Ironing</div>
    <p class="dom-text">Lorem Ipsum is simply dummy text of the printing typesetting</p>
    <div class="know">KNOW MORE <svg width="26" height="26" viewBox="0 0 26 26"><circle cx="13" cy="13" r="11.5" fill="none" stroke="#fff" stroke-width="1.5"/><path d="M11 8l5 5-5 5" fill="none" stroke="#fff" stroke-width="1.8"/></svg></div>
  </div>
  <div class="card" style="left:618px;top:117px">
    <div class="photo" role="img" aria-label="Photo of steam cleaning a tiled floor" style="background:linear-gradient(135deg,#e6e6e6,#8c8c8c)"></div>
    <div class="dom-title">Tiled Floor Steam Clean</div>
    <p class="dom-text">Lorem Ipsum is simply dummy text of the printing typesetting</p>
    <div class="know">KNOW MORE <svg width="26" height="26" viewBox="0 0 26 26"><circle cx="13" cy="13" r="11.5" fill="none" stroke="#fff" stroke-width="1.5"/><path d="M11 8l5 5-5 5" fill="none" stroke="#fff" stroke-width="1.8"/></svg></div>
  </div>
  <div class="card" style="left:882px;top:117px">
    <div class="photo" role="img" aria-label="Photo of an end of tenancy clean" style="background:linear-gradient(135deg,#8a6a44,#3d2c1c)"></div>
    <div class="dom-title">Tenancy Clean</div>
    <p class="dom-text">Lorem Ipsum is simply dummy text of the printing typesetting</p>
    <div class="know">KNOW MORE <svg width="26" height="26" viewBox="0 0 26 26"><circle cx="13" cy="13" r="11.5" fill="none" stroke="#fff" stroke-width="1.5"/><path d="M11 8l5 5-5 5" fill="none" stroke="#fff" stroke-width="1.8"/></svg></div>
  </div>
</section>

<section class="commercial">
  <h2 class="heading" style="top:1617px">COMMERCIAL <span>SERVICES</span></h2>
  <div class="card" style="left:77px;top:1694px">
    <div class="photo" role="img" aria-label="Photo of office vacuuming" style="height:166px;background:linear-gradient(135deg,#f0eeea,#9a6a44)"></div>
    <div class="com-title">Vacuuming</div>
    <p class="com-text">Lorem Ipsum is simply dummy text of the printing typesetting</p>
    <div class="more">More</div><div class="com-rule"></div>
  </div>
  <div class="card" style="left:346px;top:1694px">
    <div class="photo" role="img" aria-label="Photo of desk polishing" style="height:166px;background:linear-gradient(135deg,#f4f2ee,#e6c24a)"></div>
    <div class="com-title">Desk polishing</div>
    <p class="com-text">Lorem Ipsum is simply dummy text of the printing typesetting</p>
    <div class="more">More</div><div class="com-rule"></div>
  </div>
  <div class="card" style="left:618px;top:1694px">
    <div class="photo" role="img" aria-label="Photo of bin emptying outdoors" style="height:166px;background:linear-gradient(135deg,#c9c9c4,#6f7a62)"></div>
    <div class="com-title">Bin emptying</div>
    <p class="com-text">Lorem Ipsum is simply dummy text of the printing typesetting</p>
    <div class="more">More</div><div class="com-rule"></div>
  </div>
  <div class="card" style="left:882px;top:1694px">
    <div class="photo" role="img" aria-label="Photo of washroom cleaning" style="height:166px;background:linear-gradient(135deg,#eef0f4,#7b8cab)"></div>
    <div class="com-title">Toilet cleaning</div>
    <p class="com-text">Lorem Ipsum is simply dummy text of the printing typesetting</p>
    <div class="more">More</div><div class="com-rule"></div>
  </div>
</section>

<section class="testimonial">
  <h2 class="t-head">WHAT OUR<br>CLIENT SAY</h2>
  <div class="t-divider"></div>
  <div class="abs" role="img" aria-label="Portrait photo of the client" style="left:421px;top:64px;width:124px;height:124px;background:linear-gradient(135deg,#e9ecef,#b9c3cf)"></div>
  <p class="t-text">Lorem Ipsum is simply dummy text of the printing and typesetting industry.<br>Lorem Ipsum has been the industry's standard dummy text ever.<br><span style="font-size:13px">-ANNA ROWE</span></p>
  <div class="dots" style="left:519px;top:230px;gap:4px">
    <i style="width:15px;height:15px;border:1.5px solid #fff"></i><i class="on" style="width:15px;height:15px;background:var(--navy);border:1.5px solid #fff"></i><i style="width:15px;height:15px;border:1.5px solid #fff"></i><i style="width:15px;height:15px;border:1.5px solid #fff"></i><i style="width:15px;height:15px;border:1.5px solid #fff"></i><i style="width:15px;height:15px;border:1.5px solid #fff"></i>
  </div>
</section>

<section class="contact">
  <h2 class="heading" style="top:2397px;letter-spacing:3px">CONTACT <span style="color:var(--navy)">US</span></h2>
  <p class="intro" style="top:2468px;font-size:14.5px;line-height:28px;color:#444">Lorem Ipsum is simply dummy text of the printing and typesetting industry. Lorem Ipsum has been the industry's standard dummy text ever.</p>
  <div class="field" style="left:287px;top:2559px;width:311px;height:42px">Name</div>
  <div class="field" style="left:287px;top:2612px;width:311px;height:42px">Email Id</div>
  <div class="field" style="left:287px;top:2663px;width:311px;height:42px">Mo. No.</div>
  <div class="field" style="left:287px;top:2716px;width:311px;height:42px">Subject Name</div>
  <div class="field" style="left:609px;top:2559px;width:311px;height:199px">Message here</div>
  <div class="btn" style="left:510px;top:2789px;width:187px;height:50px;border-radius:0">Submit</div>
</section>

<footer class="footer">
  <div class="f-head" style="left:79px">Usfull links</div>
  <div class="f-head" style="left:287px">BLOG POST</div>
  <div class="f-head" style="left:598px">Latest News</div>
  <div class="f-head" style="left:867px">Contact Information</div>
  <div class="f-links">
    <a style="top:110px">Home</a><a style="top:148px">About</a><a style="top:185px">Services</a><a style="top:222px">Blog</a><a style="top:260px">Contact</a>
  </div>
  <div class="f-post" style="top:106px"><div class="f-thumb" role="img" aria-label="Author photo"></div><p>Lorem Ipsum is simply dummy text of<br>Today 5:60 pm-12.06.2016</p></div>
  <div class="f-post" style="top:212px"><div class="f-thumb" role="img" aria-label="Author photo"></div><p>Lorem Ipsum is simply dummy text of<br>Today 5:60 pm-12.06.2016</p></div>
  <p class="f-news" style="top:106px">We only buy and renovate homes in our neighborhood<br>April 18th,2016</p>
  <div class="f-read" style="top:175px">READ MORE</div>
  <p class="f-news" style="top:214px">We are a team of experienced home buyers.<br>March 23rd,2016</p>
  <div class="f-read" style="top:287px">READ MORE</div>
  <p class="f-contact" style="top:100px">Lorem Ipsum is simply dummy text of the printing and typesetting industry.</p>
  <p class="f-contact" style="top:178px">012-555-0148</p>
  <p class="f-contact" style="top:213px">info@brightmorrow.example</p>
</footer>
<div class="social" style="left:868px;background:var(--sky)"></div>
<div class="social" style="left:950px;background:var(--white)"></div>
<div class="social" style="left:1034px;background:var(--white)"></div>
<div class="bottom">©&nbsp; BRIGHT MORROW LTD - 2015. All rights reserved</div>

</body>
</html>
```